Hospitality project presentation

I am developing a hospitality project and I need to present to the developer an outstanding presentation highlighting the overall look and feel. I will provide the text and most of the pictures (not all of them) some pictures (copyright free) will hae to be provided by the designer. Maximum number of pages 15, and zoom calls with me to make some adjustment if needed.

Hospitality

• calibri light

• 15 slides
• Hospitality resort project look and feel

```html
<!DOCTYPE html>
<html lang="en">
<head>
<meta charset="utf-8">
<title>Hospitality Project – Presentation Look and Feel</title>
<link href="https://fonts.googleapis.com/css2?family=Carlito:wght@400;700&display=swap" rel="stylesheet">
<style>
:root{
  --cyan:#14d2ea;
  --teal:#25a6b4;
  --orange:#f07a12;
  --yellow:#f6b800;
  --green:#4d5c12;
  --ink:#1c1c1c;
  --grey:#7a7a7a;
  --panel:#eeeeee;
  --page:#ffffff;
}
*{margin:0;padding:0;box-sizing:border-box}
html,body{width:1200px;height:1200px;overflow:hidden;background:var(--page)}
body{position:relative;font-family:"Carlito","Calibri",sans-serif;color:var(--ink)}
.slide{position:absolute;width:305px;height:172px;background:#fff;overflow:hidden;box-shadow:0 4px 12px rgba(0,0,0,.22)}
.abs{position:absolute}
.ph{position:absolute}
.brand{position:absolute;left:24px;top:11px;display:flex;align-items:center;gap:2px;font-size:3.6px;color:var(--orange);white-space:nowrap}
.brand i{display:block;width:4px;height:4px;background:var(--orange)}
.brand.right{left:auto;right:22px}
.dots{position:absolute;right:22px;top:14px;display:flex;gap:1.3px}
.dots.left{right:auto;left:22px}
.dots b{display:block;width:2px;height:2px;border-radius:50%;background:var(--orange)}
.dots b:nth-child(2){background:var(--cyan)}
.dots b:nth-child(3){background:#666}
.dots b:nth-child(4){background:#ccc}
.foot{position:absolute;left:23px;top:162px;font-size:2.6px;color:var(--grey)}
.foot-line{position:absolute;left:216px;top:164px;width:46px;height:.5px;background:var(--cyan)}
.pnum{position:absolute;left:280px;top:162px;font-size:2.6px;color:var(--grey)}
.title{position:absolute;font-size:13px;line-height:1.05;font-weight:400;color:var(--ink)}
.sub{position:absolute;font-size:6.2px;color:var(--cyan)}
.body{position:absolute;font-size:2.6px;line-height:1.35;color:#333;text-align:justify}
.lbl{font-size:4px;color:var(--cyan)}
.icon{position:absolute;width:14px;height:14px;border-radius:2px;background:#fff;box-shadow:0 1px 3px rgba(0,0,0,.25);display:flex;align-items:center;justify-content:center}
.icon.on{background:var(--cyan)}
.icon svg{width:8px;height:8px}
.small-title{font-size:3.4px;font-weight:700;color:#222}
</style>
</head>
<body>

<!-- Slide 1: cover -->
<section class="slide" style="left:102px;top:50px;background:linear-gradient(180deg,#cfe3ee 0%,#e9eef0 55%,#e8dccb 100%)">
  <div class="ph" role="img" aria-label="Aerial photograph of a tropical resort pool and palm trees by the ocean" style="left:0;top:0;width:160px;height:172px;background:linear-gradient(160deg,#4a8fb3 0%,#2c6f87 40%,#3ba7b5 70%,#6f8f6a 100%);border-radius:0 0 0 0;clip-path:path('M0 0 H140 C118 40 118 70 140 100 C160 130 150 155 150 172 H0 Z')"></div>
  <div class="ph" role="img" aria-label="Sea foam washing onto a sandy beach" style="left:180px;top:118px;width:125px;height:54px;background:linear-gradient(180deg,#e9f1f2,#d9cdb9)"></div>
  <div class="dots"><b></b><b></b><b></b><b></b></div>
  <h1 class="title" style="left:146px;top:66px;width:150px;font-size:17.5px;text-align:center;color:#1f1f1f">Your Hospitality<br>Project title here</h1>
  <p class="sub" style="left:150px;top:115px;width:142px;text-align:center;font-size:5.8px;color:#19a9c8">Your Hospitality subtitle Project goes here</p>
  <div class="brand" style="left:34px;top:141px;color:#fff;font-size:5px"><i style="background:#fff"></i>Sandbay Resort</div>
</section>

<!-- Slide 2 -->
<section class="slide" style="left:451px;top:50px">
  <div class="abs" style="left:144px;top:0;width:161px;height:172px;background:var(--cyan)"></div>
  <div class="brand"><i></i>Sandbay Resort</div>
  <div class="dots"><b style="background:var(--orange)"></b><b style="background:var(--orange)"></b><b style="background:#fff"></b><b style="background:#fff"></b></div>
  <div class="ph" role="img" aria-label="Waiter setting a restaurant table with flowers and glasses" style="left:0;top:39px;width:181px;height:93px;background:linear-gradient(120deg,#e3d6c8,#8c6b52 45%,#2f2a28 70%,#b9a38a);border:2px solid #fff"></div>
  <h2 class="title" style="left:198px;top:39px;color:#fff;font-size:13px">Your title slide</h2>
  <p class="sub" style="left:198px;top:54px;color:#fff;font-size:4.2px">Lorem Ipsum is simply dummy text</p>
  <div class="icon" style="left:196px;top:74px;width:16px;height:16px"><svg viewBox="0 0 10 10"><path d="M1 7h8M2 7a3 3 0 0 1 6 0M5 3.5v-1" stroke="#111" stroke-width="1.2" fill="none"/></svg></div>
  <div class="abs" style="left:217px;top:74px;width:60px"><div class="lbl" style="color:#fff">Your subtitle slide</div><p class="body" style="position:static;color:#fff;font-size:2.4px">Lorem ipsum is simply dummy text of the printing and typesetting industry.</p></div>
  <div class="icon" style="left:196px;top:108px;width:16px;height:16px"><svg viewBox="0 0 10 10"><circle cx="5" cy="3" r="2" fill="#111"/><path d="M1.5 9.5c0-3 7-3 7 0z" fill="#111"/></svg></div>
  <div class="abs" style="left:217px;top:108px;width:60px"><div class="lbl" style="color:#fff">Your subtitle slide</div><p class="body" style="position:static;color:#fff;font-size:2.4px">Lorem ipsum is simply dummy text of the printing and typesetting industry.</p></div>
  <p class="foot">Hospitality project name here</p>
  <div class="foot-line" style="background:#fff"></div>
  <p class="pnum" style="color:#fff">2</p>
</section>

<!-- Slide 3 -->
<section class="slide" style="left:800px;top:50px">
  <div class="ph" role="img" aria-label="Turquoise-tinted restaurant dining room" style="left:0;top:105px;width:305px;height:67px;background:linear-gradient(90deg,#1aa4b0,#2bb8c4 50%,#149aa8);clip-path:path('M0 18 C60 0 110 0 160 18 C210 36 260 28 305 8 V67 H0 Z')"></div>
  <div class="brand"><i></i>Sandbay Resort</div>
  <div class="dots"><b></b><b></b><b></b><b></b></div>
  <div class="ph" role="img" aria-label="Waiter setting a restaurant table" style="left:37px;top:45px;width:90px;height:90px;border-radius:50%;border:2px solid #fff;background:radial-gradient(circle at 60% 40%,#3a2d26,#a88c70 60%,#e0d2c2)"></div>
  <div class="ph" role="img" aria-label="Plated dessert on a dinner table" style="left:141px;top:96px;width:40px;height:40px;border-radius:50%;border:2px solid #fff;background:radial-gradient(circle,#b2483b,#e8d8c8 70%)"></div>
  <div class="ph" role="img" aria-label="Plated salad with flowers" style="left:196px;top:96px;width:40px;height:40px;border-radius:50%;border:2px solid #fff;background:radial-gradient(circle,#d48c2a,#5a6b3a 70%)"></div>
  <h2 class="title" style="left:155px;top:33px;font-size:12px">Your title slide here</h2>
  <p class="sub" style="left:155px;top:47px;font-size:5.6px">Lorem Ipsum simple dummy text</p>
  <p class="body" style="left:155px;top:57px;width:102px">Lorem ipsum is simply dummy text of the printing and typesetting industry. Lorem ipsum has been the industry's standard dummy text ever since the 1500s, when an unknown printer took a galley of type and scrambled it to make a specimen book.</p>
  <p class="foot" style="color:#fff">Hospitality project name here</p>
</section>

<!-- Slide 4 -->
<section class="slide" style="left:102px;top:237px">
  <div class="brand"><i></i>Sandbay Resort</div>
  <div class="dots"><b></b><b></b><b></b><b></b></div>
  <h2 class="title" style="left:31px;top:30px;font-size:12.5px">Your title<br>slide here</h2>
  <p class="sub" style="left:31px;top:60px;font-size:5.2px">Lorem Ipsum dummy text</p>
  <p class="body" style="left:31px;top:70px;width:76px">Lorem ipsum is simply dummy text of the printing and typesetting industry. Lorem ipsum has been the industry's standard dummy text.</p>
  <div class="icon on" style="left:28px;top:99px"><svg viewBox="0 0 10 10"><path d="M2 8V5h3l1-3h2v6z" fill="#fff"/></svg></div>
  <div class="abs" style="left:46px;top:99px;width:56px"><div class="lbl">Your subtitle slide</div><p class="body" style="position:static">Lorem ipsum is simply dummy text of the printing and typesetting industry.</p></div>
  <div class="icon" style="left:28px;top:132px"><svg viewBox="0 0 10 10"><circle cx="5" cy="5" r="3.6" fill="none" stroke="#111" stroke-width="1.2"/><path d="M5 1.4V8.6M1.4 5H8.6" stroke="#111" stroke-width=".8"/></svg></div>
  <div class="abs" style="left:46px;top:132px;width:56px"><div class="lbl">Your subtitle slide</div><p class="body" style="position:static">Lorem ipsum is simply dummy text of the printing and typesetting industry.</p></div>
  <div class="ph" role="img" aria-label="Slice of layered berry cake" style="left:145px;top:24px;width:51px;height:34px;background:linear-gradient(135deg,#f2d6c6,#c0394a 60%,#3a2a28)"></div>
  <div class="ph" role="img" aria-label="Burger with melted cheese on a board" style="left:145px;top:60px;width:51px;height:98px;background:linear-gradient(180deg,#3a3330,#d08a2e 40%,#7a3a24 70%,#5a3a26)"></div>
  <div class="ph" role="img" aria-label="Tacos with lime and herbs" style="left:198px;top:24px;width:86px;height:96px;background:linear-gradient(150deg,#3b2f26,#d9902e 45%,#7aa03a 70%,#3a2a20)"></div>
  <div class="ph" role="img" aria-label="Pizza slices on a table" style="left:198px;top:122px;width:86px;height:36px;background:linear-gradient(120deg,#c46a2c,#e8b45a 50%,#7a3a20)"></div>
  <p class="foot">Hospitality project name here</p><div class="foot-line"></div><p class="pnum">4</p>
</section>

<!-- Slide 5 -->
<section class="slide" style="left:451px;top:237px">
  <div class="brand"><i></i>Sandbay Resort</div>
  <div class="dots"><b></b><b></b><b></b><b></b></div>
  <div class="abs" style="left:14px;top:28px;width:277px;height:66px;background:var(--panel)"></div>
  <div class="ph" role="img" aria-label="Beach loungers and umbrella at sunset" style="left:22px;top:38px;width:69px;height:45px;background:linear-gradient(180deg,#e7c9a0,#5d7f8e 50%,#5c4632)"></div>
  <div class="ph" role="img" aria-label="Palm trees reflected in a resort pool" style="left:99px;top:38px;width:70px;height:45px;background:linear-gradient(180deg,#c7dff0,#4c7a3c 45%,#35a8c8)"></div>
  <div class="ph" role="img" aria-label="Resort pools along a tropical coastline" style="left:178px;top:38px;width:106px;height:45px;background:linear-gradient(180deg,#6fa6d6,#2b6a92 40%,#3f8a52 65%,#46b8c6)"></div>
  <p class="abs" style="left:14px;top:110px;width:277px;text-align:center;font-size:8.8px;line-height:1.2">Your extended title slide goes here, the space is interactive you<br><span style="color:var(--cyan)">could include all the text you need, the text shrink on overflow</span></p>
  <p class="body" style="left:24px;top:134px;width:257px;text-align:center">Lorem ipsum is simply dummy text of the printing and typesetting industry. Lorem ipsum has been the industry's standard dummy text ever since the 1500s, when an unknown printer took a galley of type and scrambled it to make a type specimen book. It has survived not only five centuries, but also the leap into electronic typesetting, remaining essentially unchanged.</p>
  <p class="foot">Hospitality project name here</p><div class="foot-line"></div><p class="pnum">5</p>
</section>

<!-- Slide 6 -->
<section class="slide" style="left:800px;top:237px">
  <div class="ph" role="img" aria-label="Resort villa with pool lit at dusk under a blue sky" style="left:150px;top:0;width:155px;height:172px;background:linear-gradient(180deg,#1f5fc4,#3a86d8 35%,#1a3a6a 60%,#1c6fa8 80%,#0f2f5a);clip-path:path('M38 0 H155 V172 H0 C10 140 10 110 40 80 C60 55 55 20 38 0 Z')"></div>
  <div class="brand"><i></i>Sandbay Resort</div>
  <div class="dots"><b></b><b></b><b style="background:#fff"></b><b style="background:#fff"></b></div>
  <h2 class="title" style="left:23px;top:33px;font-size:13px">Here your title slide</h2>
  <p class="sub" style="left:23px;top:50px">Lorem Ipsum is simply dummy text</p>
  <div class="icon on" style="left:22px;top:74px;width:24px;height:23px"><svg viewBox="0 0 10 10"><path d="M1 3v5M9 6v2M1 6h8M3 4.5h6v1.5" stroke="#fff" stroke-width="1" fill="none"/></svg></div>
  <div class="icon" style="left:56px;top:74px;width:24px;height:23px"><svg viewBox="0 0 10 10"><rect x="2" y="3" width="4" height="5" fill="#111"/><path d="M7 2v6" stroke="#111"/></svg></div>
  <div class="icon" style="left:90px;top:74px;width:24px;height:23px"><svg viewBox="0 0 10 10"><circle cx="5" cy="3" r="2" fill="#111"/><path d="M1.5 9.5c0-3 7-3 7 0z" fill="#111"/></svg></div>
  <div class="icon" style="left:124px;top:74px;width:24px;height:23px"><svg viewBox="0 0 10 10"><circle cx="7" cy="3" r="1.2" fill="#111"/><path d="M1 8q2-1 4 0t4 0M2 6l3-2 2 2" stroke="#111" fill="none"/></svg></div>
  <p class="body" style="left:22px;top:109px;width:128px">Lorem ipsum is simply dummy text of the printing and typesetting industry. Lorem ipsum has been the industry's standard dummy text ever since the 1500s, when an unknown printer took a galley of type and scrambled it to make a type specimen book. It has survived not only five centuries, but also the leap into electronic typesetting, remaining essentially unchanged. It was popularised in the 1960s with the release of Letraset sheets.</p>
  <p class="foot">Hospitality project name here</p>
</section>

<!-- Slide 7 -->
<section class="slide" style="left:102px;top:424px">
  <div class="brand"><i></i>Sandbay Resort</div>
  <div class="dots"><b></b><b></b><b></b><b></b></div>
  <div class="abs" style="left:16px;top:22px;width:134px;height:134px;border-radius:50%;background:#ececec"></div>
  <div class="ph" role="img" aria-label="Stack of pancakes with syrup being poured" style="left:25px;top:19px;width:94px;height:94px;border-radius:50%;background:radial-gradient(circle at 55% 60%,#d69038,#3a3a3e 60%,#2a2a2e)"></div>
  <div class="ph" role="img" aria-label="Plated gourmet dish with wine glass" style="left:84px;top:75px;width:66px;height:66px;border-radius:50%;border:2px solid #fff;background:radial-gradient(circle,#b67a3a,#3a2a20 70%)"></div>
  <h2 class="title" style="left:171px;top:56px;font-size:12px">Here your title slide</h2>
  <p class="sub" style="left:171px;top:70px;font-size:5px">Lorem Ipsum is simply dummy text</p>
  <p class="body" style="left:171px;top:84px;width:108px">Lorem ipsum is simply dummy text of the printing and typesetting industry. Lorem ipsum has been the industry's standard dummy text ever since the 1500s, when an unknown printer took a galley of type and scrambled it to make a type specimen book. It has survived not only five centuries, but also the leap into electronic typesetting, remaining essentially unchanged.</p>
  <p class="foot">Hospitality project name here</p><div class="foot-line"></div><p class="pnum">7</p>
</section>

<!-- Slide 8 -->
<section class="slide" style="left:451px;top:424px">
  <div class="brand"><i></i>Sandbay Resort</div>
  <div class="dots"><b></b><b></b><b></b><b></b></div>
  <h2 class="title" style="left:0;top:11px;width:305px;text-align:center;font-size:12.5px">Here your title slide</h2>
  <p class="sub" style="left:0;top:26px;width:305px;text-align:center;font-size:5.2px">Lorem Ipsum is simply dummy text</p>
  <div class="ph" role="img" aria-label="Ocean horizon at sunset with waves on the shore" style="left:0;top:39px;width:305px;height:56px;background:linear-gradient(180deg,#eac9ae,#d8b79e 30%,#5f8f9e 55%,#3e8a98 75%,#e6e2d6)"></div>
  <div class="icon on" style="left:31px;top:89px;width:24px;height:24px"><svg viewBox="0 0 10 10"><circle cx="7" cy="3" r="1.2" fill="#fff"/><path d="M1 8q2-1 4 0t4 0M2 6l3-2 2 2" stroke="#fff" fill="none"/></svg></div>
  <div class="icon" style="left:85px;top:89px;width:24px;height:24px"><svg viewBox="0 0 10 10"><path d="M1 4h8M2 6h6M3 8h4" stroke="#111" stroke-width="1"/></svg></div>
  <div class="icon" style="left:138px;top:89px;width:24px;height:24px"><svg viewBox="0 0 10 10"><path d="M2 2l5 6M1 8h8" stroke="#111" stroke-width="1"/></svg></div>
  <div class="icon" style="left:192px;top:89px;width:24px;height:24px"><svg viewBox="0 0 10 10"><path d="M1 6l8-2M5 2v6" stroke="#111" stroke-width="1"/></svg></div>
  <div class="icon" style="left:247px;top:89px;width:24px;height:24px"><svg viewBox="0 0 10 10"><path d="M5 1v6L2 7zM5.5 2l3 5h-3zM1 8h8" fill="#111" stroke="#111" stroke-width=".5"/></svg></div>
  <div class="abs" style="left:19px;top:118px;width:48px;text-align:center"><div class="lbl">Your subtitle slide</div><p class="body" style="position:static">Lorem ipsum is simply dummy text of the printing and typesetting industry.</p></div>
  <div class="abs" style="left:73px;top:118px;width:48px;text-align:center"><div class="lbl">Your subtitle slide</div><p class="body" style="position:static">Lorem ipsum is simply dummy text of the printing and typesetting industry.</p></div>
  <div class="abs" style="left:126px;top:118px;width:48px;text-align:center"><div class="lbl">Your subtitle slide</div><p class="body" style="position:static">Lorem ipsum is simply dummy text of the printing and typesetting industry.</p></div>
  <div class="abs" style="left:180px;top:118px;width:48px;text-align:center"><div class="lbl">Your subtitle slide</div><p class="body" style="position:static">Lorem ipsum is simply dummy text of the printing and typesetting industry.</p></div>
  <div class="abs" style="left:235px;top:118px;width:48px;text-align:center"><div class="lbl">Your subtitle slide</div><p class="body" style="position:static">Lorem ipsum is simply dummy text of the printing and typesetting industry.</p></div>
  <p class="foot">Hospitality project name here</p><div class="foot-line"></div><p class="pnum">8</p>
</section>

<!-- Slide 9 -->
<section class="slide" style="left:800px;top:424px">
  <div class="brand"><i></i>Sandbay Resort</div>
  <div class="dots"><b></b><b></b><b></b><b></b></div>
  <div class="abs" style="left:15px;top:23px;width:180px;height:134px;background:var(--panel)"></div>
  <div class="ph" role="img" aria-label="Beach at sunset with an orange overlay" style="left:21px;top:25px;width:73px;height:63px;background:linear-gradient(160deg,#e9a35a,#c9772c 60%,#a5602a)"></div>
  <p class="abs" style="left:29px;top:37px;color:#fff;font-size:8px;line-height:1.2">Place Here<br>your dummy<br>subtitle slide</p>
  <div class="ph" role="img" aria-label="Palm trees around a resort pool" style="left:97px;top:25px;width:92px;height:63px;background:linear-gradient(180deg,#c8def0,#4d7a3c 45%,#38a6c2)"></div>
  <div class="ph" role="img" aria-label="Resort building and pool at night" style="left:21px;top:91px;width:73px;height:62px;background:linear-gradient(180deg,#1d4fb0,#2c6fd0 45%,#122c56 70%,#1a7ac0)"></div>
  <div class="ph" role="img" aria-label="Aerial view of resort pools and coast" style="left:97px;top:91px;width:74px;height:62px;background:linear-gradient(160deg,#2f9fc8,#4a8a52 50%,#4fc0cc)"></div>
  <h2 class="title" style="left:204px;top:34px;font-size:11.5px">Place Here<br>your title slide</h2>
  <p class="sub" style="left:204px;top:60px;font-size:5px;line-height:1.2">Lorem Ipsum is simply<br>dummy text</p>
  <p class="body" style="left:204px;top:92px;width:78px">Lorem ipsum is simply dummy text of the printing and typesetting industry. Lorem ipsum has been the industry's standard dummy text ever since the 1500s, when an unknown printer took a galley of type and scrambled it to make a type specimen book. It has survived not only five centuries, but also the leap into electronic typesetting.</p>
  <p class="foot">Hospitality project name here</p><div class="foot-line"></div><p class="pnum">9</p>
</section>

<!-- Slide 10 -->
<section class="slide" style="left:102px;top:611px">
  <div class="brand"><i></i>Sandbay Resort</div>
  <div class="dots"><b></b><b></b><b></b><b></b></div>
  <h2 class="title" style="left:23px;top:40px;font-size:13.5px">Place Here<br>your title slide</h2>
  <p class="sub" style="left:23px;top:73px;font-size:5px">Lorem Ipsum is simply dummy text</p>
  <div class="ph" role="img" aria-label="Sunset over the sea and beach" style="left:130px;top:31px;width:83px;height:58px;background:linear-gradient(180deg,#d6d8dc,#e8c7a2 40%,#5e96a6 65%,#e3dccf)"></div>
  <div class="ph" role="img" aria-label="Aerial view of a resort pool by the sea" style="left:218px;top:31px;width:66px;height:58px;background:linear-gradient(160deg,#2e7aa8,#3c7a48 50%,#3fb2c4)"></div>
  <div class="ph" role="img" aria-label="Palm trees reflected in a pool" style="left:21px;top:94px;width:103px;height:58px;background:linear-gradient(180deg,#bdd8ee,#4c7a3c 45%,#38a6c2)"></div>
  <div class="ph" role="img" aria-label="Beach loungers at sunset" style="left:130px;top:94px;width:66px;height:58px;background:linear-gradient(180deg,#e8caa2,#6a8e9a 50%,#5a4430)"></div>
  <div class="ph" role="img" aria-label="Resort and pool at night" style="left:201px;top:94px;width:83px;height:58px;background:linear-gradient(180deg,#1f52b4,#2d70d0 45%,#13305c 70%,#1a7cc2)"></div>
  <p class="foot">Hospitality project name here</p><div class="foot-line"></div><p class="pnum">10</p>
</section>

<!-- Slide 11 -->
<section class="slide" style="left:451px;top:611px">
  <div class="brand right"><i></i>Sandbay Resort</div>
  <div class="dots left"><b></b><b></b><b></b><b></b></div>
  <div class="abs" style="left:21px;top:12px;width:132px;height:148px;background:var(--panel)"></div>
  <div class="ph" role="img" aria-label="Beach and turquoise sea from above" style="left:21px;top:16px;width:84px;height:139px;background:linear-gradient(180deg,#e6d8ca,#9fc2cc 35%,#3ea4b6 55%,#d9cdb8)"></div>
  <div class="ph" role="img" aria-label="Resort restaurant interior" style="left:104px;top:23px;width:42px;height:38px;border:1.5px solid #fff;background:linear-gradient(160deg,#5a3a2a,#b06a3a 60%,#3a2a20)"></div>
  <div class="ph" role="img" aria-label="Resort pool by the sea" style="left:104px;top:67px;width:42px;height:37px;border:1.5px solid #fff;background:linear-gradient(180deg,#7ab0d8,#3a7a4a 45%,#40b0c4)"></div>
  <div class="ph" role="img" aria-label="Resort bedroom suite" style="left:104px;top:111px;width:42px;height:37px;border:1.5px solid #fff;background:linear-gradient(160deg,#d8ccbc,#8a6a4e 60%,#4a3a2e)"></div>
  <h2 class="title" style="left:164px;top:35px;font-size:13px">Your title slide here</h2>
  <p class="sub" style="left:164px;top:50px;font-size:5.8px">Lorem Ipsum simple dummy text</p>
  <p class="body" style="left:164px;top:62px;width:120px">Lorem ipsum is simply dummy text of the printing and typesetting industry. Lorem ipsum has been the industry's standard dummy text ever since the 1500s, when an unknown printer took a galley of type and scrambled it to make a type specimen book. It has survived not only five centuries, but also</p>
  <div class="abs" style="left:164px;top:112px;width:30px;text-align:center"><div style="font-size:18px;font-weight:700;color:var(--orange);line-height:1">6</div><div style="font-size:3.6px;color:#555;margin-top:3px">Restaurants</div></div>
  <div class="abs" style="left:204px;top:112px;width:30px;text-align:center"><div style="font-size:18px;font-weight:700;color:var(--cyan);line-height:1">10</div><div style="font-size:3.6px;color:#555;margin-top:3px">pools</div></div>
  <div class="abs" style="left:245px;top:112px;width:40px;text-align:center"><div style="font-size:18px;font-weight:700;color:var(--green);line-height:1">500</div><div style="font-size:3.6px;color:#555;margin-top:3px">rooms</div></div>
  <p class="foot">Hospitality project name here</p><div class="foot-line"></div><p class="pnum">11</p>
</section>

<!-- Slide 12 -->
<section class="slide" style="left:800px;top:611px">
  <div class="brand"><i></i>Sandbay Resort</div>
  <div class="dots"><b></b><b></b><b></b><b></b></div>
  <h2 class="title" style="left:0;top:14px;width:305px;text-align:center;font-size:14px">Meet the Crew</h2>
  <p class="sub" style="left:0;top:31px;width:305px;text-align:center;font-size:5.8px">Lorem Ipsum simple dummy text</p>
  <div class="abs" style="left:16px;top:54px;width:275px;height:85px;background:var(--panel)"></div>
  <div class="ph" role="img" aria-label="Portrait of a team member" style="left:39px;top:59px;width:49px;height:63px;background:linear-gradient(180deg,#d9d9d9,#8a8f96 60%,#2a2c30)"></div>
  <div class="ph" role="img" aria-label="Portrait of a team member" style="left:98px;top:59px;width:49px;height:63px;background:linear-gradient(180deg,#d6dbe0,#9c9ea4 60%,#4a4c52)"></div>
  <div class="ph" role="img" aria-label="Portrait of a team member" style="left:158px;top:59px;width:48px;height:63px;background:linear-gradient(180deg,#c4b4a4,#7a6656 60%,#2e2c32)"></div>
  <div class="ph" role="img" aria-label="Portrait of a team member" style="left:218px;top:59px;width:48px;height:63px;background:linear-gradient(180deg,#d08a4a,#b89a82 60%,#5a5a60)"></div>
  <div class="abs" style="left:34px;top:124px;width:59px;text-align:center;font-size:5px;line-height:1.05"><span style="color:var(--cyan)">NAME<br>Surname</span><br><span style="font-size:4px;color:#555">CEO</span></div>
  <div class="abs" style="left:93px;top:124px;width:59px;text-align:center;font-size:5px;line-height:1.05"><span style="color:var(--cyan)">NAME<br>Surname</span><br><span style="font-size:4px;color:#555">CFO</span></div>
  <div class="abs" style="left:153px;top:124px;width:59px;text-align:center;font-size:5px;line-height:1.05"><span style="color:var(--cyan)">NAME<br>Surname</span><br><span style="font-size:4px;color:#555">CMO</span></div>
  <div class="abs" style="left:213px;top:124px;width:59px;text-align:center;font-size:5px;line-height:1.05"><span style="color:var(--cyan)">NAME<br>Surname</span><br><span style="font-size:4px;color:#555">CSO</span></div>
  <p class="foot">Hospitality project name here</p><div class="foot-line"></div><p class="pnum">12</p>
</section>

<!-- Slide 13: ring infographic -->
<section class="slide" style="left:102px;top:798px">
  <div class="brand right"><i></i>Sandbay Resort</div>
  <div class="dots left"><b></b><b></b><b></b><b></b></div>
  <h2 class="title" style="left:23px;top:27px;font-size:14px">Infografhic slide</h2>
  <p class="sub" style="left:23px;top:44px">Lorem Ipsum is simply dummy text</p>
  <svg class="abs" style="left:100px;top:64px" width="100" height="86" viewBox="0 0 100 86">
    <g fill="none" stroke-width="7">
      <ellipse cx="46" cy="68" rx="32" ry="10" stroke="var(--green)"/>
      <ellipse cx="46" cy="50" rx="32" ry="10" stroke="var(--orange)"/>
      <ellipse cx="46" cy="32" rx="32" ry="10" stroke="var(--teal)"/>
      <ellipse cx="46" cy="14" rx="32" ry="10" stroke="var(--yellow)"/>
    </g>
    <path d="M84 7H96M84 50H96M84 70H96" stroke="#888" stroke-width=".5"/>
  </svg>
  <svg class="abs" style="left:77px;top:74px" width="9" height="9" viewBox="0 0 10 10"><path d="M1 2h8L5 8z" fill="none" stroke="var(--yellow)"/></svg>
  <svg class="abs" style="left:77px;top:108px" width="9" height="9" viewBox="0 0 10 10"><path d="M2 1h6L2 9h6z" fill="none" stroke="var(--orange)"/></svg>
  <svg class="abs" style="left:198px;top:64px" width="9" height="9" viewBox="0 0 10 10"><circle cx="5" cy="5" r="3" fill="none" stroke="var(--green)"/></svg>
  <svg class="abs" style="left:198px;top:96px" width="9" height="9" viewBox="0 0 10 10"><circle cx="5" cy="5" r="3.5" fill="none" stroke="var(--cyan)"/><circle cx="5" cy="5" r="1.5" fill="none" stroke="var(--cyan)"/></svg>
  <svg class="abs" style="left:198px;top:130px" width="9" height="9" viewBox="0 0 10 10"><circle cx="5" cy="5" r="3" fill="none" stroke="var(--yellow)"/></svg>
  <div class="abs" style="left:36px;top:76px;width:40px;text-align:right"><div class="small-title">Dummy title text</div><p class="body" style="position:static;text-align:right">Lorem ipsum is simply dummy text of the printing and typesetting industry.</p></div>
  <div class="abs" style="left:36px;top:111px;width:40px;text-align:right"><div class="small-title">Dummy title text</div><p class="body" style="position:static;text-align:right">Lorem ipsum is simply dummy text of the printing and typesetting industry.</p></div>
  <div class="abs" style="left:211px;top:66px;width:52px"><div class="small-title">Dummy title text</div><p class="body" style="position:static;text-align:left">Lorem ipsum is simply dummy text of the printing and typesetting industry.</p></div>
  <div class="abs" style="left:211px;top:99px;width:52px"><div class="small-title">Dummy title text</div><p class="body" style="position:static;text-align:left">Lorem ipsum is simply dummy text of the printing and typesetting industry.</p></div>
  <div class="abs" style="left:211px;top:133px;width:52px"><div class="small-title">Dummy title text</div><p class="body" style="position:static;text-align:left">Lorem ipsum is simply dummy text of the printing and typesetting industry.</p></div>
  <p class="foot">Hospitality project name here</p><div class="foot-line"></div><p class="pnum">15</p>
</section>

<!-- Slide 14: process infographic -->
<section class="slide" style="left:451px;top:798px">
  <div class="brand right"><i></i>Sandbay Resort</div>
  <div class="dots left"><b></b><b></b><b></b><b></b></div>
  <h2 class="title" style="left:23px;top:27px;font-size:14px">Infografhic slide</h2>
  <p class="sub" style="left:23px;top:44px">Lorem Ipsum is simply dummy text</p>
  <svg class="abs" style="left:100px;top:62px" width="104" height="94" viewBox="0 0 104 94">
    <circle cx="21" cy="17" r="15" fill="var(--cyan)"/>
    <circle cx="80" cy="17" r="15" fill="var(--orange)"/>
    <circle cx="80" cy="75" r="15" fill="var(--green)"/>
    <circle cx="21" cy="75" r="15" fill="var(--yellow)"/>
    <g fill="none" stroke-width="1.6">
      <path d="M32 30 A26 26 0 0 1 66 27" stroke="var(--cyan)"/>
      <path d="M72 32 A26 26 0 0 1 70 64" stroke="var(--orange)"/>
      <path d="M68 70 A26 26 0 0 1 34 68" stroke="var(--green)"/>
      <path d="M29 64 A26 26 0 0 1 30 34" stroke="var(--yellow)"/>
    </g>
    <path d="M66 27l-3-3M66 27l-4 1M70 64l-3 1M70 64l0-4M34 68l3 2M34 68l1-4M30 34l3-1M30 34l-1 3" stroke="#333" stroke-width=".8"/>
    <g font-size="5" fill="#fff" font-family="Carlito,sans-serif" text-anchor="middle" font-weight="700">
      <text x="21" y="19" fill="#11414a">01</text><text x="80" y="19" fill="#5a2a04">02</text><text x="80" y="77" fill="#fff">03</text><text x="21" y="77" fill="#5a4400">04</text>
    </g>
    <text x="51" y="45" font-size="3.8" text-anchor="middle" font-family="Carlito,sans-serif" font-weight="700">Process</text>
    <text x="51" y="50" font-size="3.8" text-anchor="middle" font-family="Carlito,sans-serif" font-weight="700">infographic</text>
  </svg>
  <div class="abs" style="left:46px;top:69px;width:50px;text-align:right"><div class="small-title">Dummy title text</div><p class="body" style="position:static;text-align:right">Lorem ipsum is simply dummy text of the printing and typesetting industry.</p></div>
  <div class="abs" style="left:46px;top:129px;width:50px;text-align:right"><div class="small-title">Dummy title text</div><p class="body" style="position:static;text-align:right">Lorem ipsum is simply dummy text of the printing and typesetting industry.</p></div>
  <div class="abs" style="left:202px;top:69px;width:52px"><div class="small-title">Dummy title text</div><p class="body" style="position:static;text-align:left">Lorem ipsum is simply dummy text of the printing and typesetting industry.</p></div>
  <div class="abs" style="left:202px;top:129px;width:52px"><div class="small-title">Dummy title text</div><p class="body" style="position:static;text-align:left">Lorem ipsum is simply dummy text of the printing and typesetting industry.</p></div>
  <p class="foot">Hospitality project name here</p><div class="foot-line"></div><p class="pnum">16</p>
</section>

<!-- Slide 15: key figures -->
<section class="slide" style="left:800px;top:798px">
  <div class="brand right"><i></i>Sandbay Resort</div>
  <div class="dots left"><b></b><b></b><b></b><b></b></div>
  <h2 class="title" style="left:23px;top:27px;font-size:14px">Data slide</h2>
  <p class="sub" style="left:23px;top:44px">Lorem Ipsum is simply dummy text</p>
  <svg class="abs" style="left:28px;top:68px" width="12" height="12" viewBox="0 0 10 10"><circle cx="5" cy="5" r="3.5" fill="none" stroke="#444" stroke-width=".8"/><circle cx="5" cy="5" r="1.4" fill="none" stroke="#444" stroke-width=".8"/></svg>
  <svg class="abs" style="left:120px;top:68px" width="12" height="12" viewBox="0 0 10 10"><path d="M5 1l4 2-4 2-4-2zM1 5l4 2 4-2M1 7l4 2 4-2" fill="none" stroke="var(--cyan)" stroke-width=".8"/></svg>
  <svg class="abs" style="left:212px;top:68px" width="12" height="12" viewBox="0 0 10 10"><path d="M2 2l6 6M8 2L2 8" stroke="#444" stroke-width=".8"/><circle cx="2" cy="2" r="1" fill="#fff" stroke="#444" stroke-width=".6"/><circle cx="8" cy="8" r="1" fill="#fff" stroke="#444" stroke-width=".6"/></svg>
  <div class="abs" style="left:28px;top:86px;width:72px"><div style="font-size:12.5px">$34.000B</div><div class="small-title" style="margin-top:5px">Subtitle here</div><p class="body" style="position:static;margin-top:3px">Lorem ipsum is simply dummy text of the printing and typesetting industry. Lorem ipsum has been the industry's standard dummy text ever since the 1500s, when an unknown printer took a galley of type.</p></div>
  <div class="abs" style="left:120px;top:86px;width:72px"><div style="font-size:12.5px;color:var(--cyan)">100800</div><div class="small-title" style="margin-top:5px;color:var(--cyan)">Subtitle here</div><p class="body" style="position:static;margin-top:3px">Lorem ipsum is simply dummy text of the printing and typesetting industry. Lorem ipsum has been the industry's standard dummy text ever since the 1500s, when an unknown printer took a galley of type.</p></div>
  <div class="abs" style="left:212px;top:86px;width:72px"><div style="font-size:12.5px">53389</div><div class="small-title" style="margin-top:5px">Subtitle here</div><p class="body" style="position:static;margin-top:3px">Lorem ipsum is simply dummy text of the printing and typesetting industry. Lorem ipsum has been the industry's standard dummy text ever since the 1500s, when an unknown printer took a galley of type.</p></div>
  <p class="foot">Hospitality project name here</p><div class="foot-line"></div><p class="pnum">13</p>
</section>

<!-- Slide 16: bar chart -->
<section class="slide" style="left:102px;top:986px">
  <div class="brand right"><i></i>Sandbay Resort</div>
  <div class="dots left"><b></b><b></b><b></b><b></b></div>
  <h2 class="title" style="left:23px;top:27px;font-size:14px">Data slide</h2>
  <p class="sub" style="left:23px;top:44px">Lorem Ipsum is simply dummy text</p>
  <div class="abs" style="left:23px;top:104px;width:92px"><div class="small-title">Subtitle here</div><p class="body" style="position:static;margin-top:3px">Lorem ipsum is simply dummy text of the printing and typesetting industry. Lorem ipsum has been the industry's standard dummy text ever since the 1500s, when an unknown printer took a galley of type and scrambled it to make a type specimen book. It has survived not only five centuries, but</p></div>
  <svg class="abs" style="left:142px;top:52px" width="148" height="106" viewBox="0 0 148 106" font-family="Carlito,sans-serif">
    <g font-size="2.4" fill="#555"><rect x="42" y="2" width="2" height="2" fill="var(--cyan)"/><text x="45" y="4">Series 1</text><rect x="61" y="2" width="2" height="2" fill="var(--orange)"/><text x="64" y="4">Series 2</text><rect x="80" y="2" width="2" height="2" fill="var(--green)"/><text x="83" y="4">Series 3</text></g>
    <g stroke="#e2e2e2" stroke-width=".4"><path d="M10 11H144M10 25H144M10 39H144M10 53H144M10 67H144M10 81H144"/></g>
    <path d="M10 95H144" stroke="#999" stroke-width=".4"/>
    <g font-size="2.6" fill="#555" text-anchor="end"><text x="7" y="96">0</text><text x="7" y="82">1</text><text x="7" y="68">2</text><text x="7" y="54">3</text><text x="7" y="40">4</text><text x="7" y="26">5</text><text x="7" y="12">6</text></g>
    <g>
      <rect x="18" y="32" width="6" height="63" fill="var(--cyan)"/><rect x="25" y="61.4" width="6" height="33.6" fill="var(--orange)"/><rect x="32" y="67" width="6" height="28" fill="var(--green)"/>
      <rect x="51" y="60" width="6" height="35" fill="var(--cyan)"/><rect x="58" y="33.4" width="6" height="61.6" fill="var(--orange)"/><rect x="65" y="67" width="6" height="28" fill="var(--green)"/>
      <rect x="84" y="46" width="6" height="49" fill="var(--cyan)"/><rect x="91" y="69.8" width="6" height="25.2" fill="var(--orange)"/><rect x="98" y="53" width="6" height="42" fill="var(--green)"/>
      <rect x="117" y="32" width="6" height="63" fill="var(--cyan)"/><rect x="124" y="55.8" width="6" height="39.2" fill="var(--orange)"/><rect x="131" y="25" width="6" height="70" fill="var(--green)"/>
    </g>
    <g font-size="2.4" fill="#333" text-anchor="middle"><text x="21" y="30">4.5</text><text x="28" y="59">2.4</text><text x="35" y="65">2</text><text x="54" y="58">2.5</text><text x="61" y="31">4.4</text><text x="68" y="65">2</text><text x="87" y="44">3.5</text><text x="94" y="68">1.8</text><text x="101" y="51">3</text><text x="120" y="30">4.5</text><text x="127" y="54">2.8</text><text x="134" y="23">5</text></g>
    <g font-size="2.6" fill="#555" text-anchor="middle"><text x="28" y="100">Category 1</text><text x="61" y="100">Category 2</text><text x="94" y="100">Category 3</text><text x="127" y="100">Category 4</text></g>
  </svg>
  <p class="foot">Hospitality project name here</p><div class="foot-line"></div><p class="pnum">14</p>
</section>

<!-- Slide 17: percentage rings -->
<section class="slide" style="left:451px;top:986px">
  <div class="brand right"><i></i>Sandbay Resort</div>
  <div class="dots left"><b></b><b></b><b></b><b></b></div>
  <h2 class="title" style="left:23px;top:27px;font-size:14px">Data slide</h2>
  <p class="sub" style="left:23px;top:44px">Lorem Ipsum is simply dummy text</p>
  <svg class="abs" style="left:0;top:66px" width="305" height="52" viewBox="0 0 305 52" font-family="Carlito,sans-serif">
    <g fill="none" stroke-width="4">
      <circle cx="54" cy="26" r="21" stroke="#e6e6e6"/><circle cx="54" cy="26" r="21" stroke="var(--cyan)" stroke-dasharray="66 132" transform="rotate(-90 54 26)"/>
      <circle cx="116" cy="26" r="21" stroke="#e6e6e6"/><circle cx="116" cy="26" r="21" stroke="var(--orange)" stroke-dasharray="39.6 132" transform="rotate(-90 116 26)"/>
      <circle cx="179" cy="26" r="21" stroke="#e6e6e6"/><circle cx="179" cy="26" r="21" stroke="var(--yellow)" stroke-dasharray="26.4 132" transform="rotate(-90 179 26)"/>
      <circle cx="243" cy="26" r="21" stroke="#e6e6e6"/><circle cx="243" cy="26" r="21" stroke="var(--teal)" stroke-dasharray="99 132" transform="rotate(-90 243 26)"/>
    </g>
    <g font-size="9" font-weight="700" text-anchor="middle" fill="#1c1c1c"><text x="54" y="29">50%</text><text x="116" y="29">30%</text><text x="179" y="29">20%</text><text x="243" y="29">75%</text></g>
  </svg>
  <div class="abs" style="left:31px;top:124px;width:48px"><div class="small-title">Data title here</div><p class="body" style="position:static;margin-top:2px">Lorem ipsum is simply dummy text of the printing and typesetting industry. Lorem ipsum has been</p></div>
  <div class="abs" style="left:96px;top:124px;width:48px"><div class="small-title">Data title here</div><p class="body" style="position:static;margin-top:2px">Lorem ipsum is simply dummy text of the printing and typesetting industry. Lorem ipsum has been</p></div>
  <div class="abs" style="left:162px;top:124px;width:48px"><div class="small-title">Data title here</div><p class="body" style="position:static;margin-top:2px">Lorem ipsum is simply dummy text of the printing and typesetting industry. Lorem ipsum has been</p></div>
  <div class="abs" style="left:228px;top:124px;width:48px"><div class="small-title">Data title here</div><p class="body" style="position:static;margin-top:2px">Lorem ipsum is simply dummy text of the printing and typesetting industry. Lorem ipsum has been</p></div>
  <p class="foot">Hospitality project name here</p><div class="foot-line"></div><p class="pnum">17</p>
</section>

<!-- Slide 18: pie chart -->
<section class="slide" style="left:800px;top:986px">
  <div class="brand right"><i></i>Sandbay Resort</div>
  <div class="dots left"><b></b><b></b><b></b><b></b></div>
  <h2 class="title" style="left:23px;top:27px;font-size:14px">Data slide</h2>
  <p class="sub" style="left:23px;top:44px">Lorem Ipsum is simply dummy text</p>
  <div class="abs" style="left:23px;top:63px;width:122px"><div class="small-title">Subtitle here</div><p class="body" style="position:static;margin-top:3px">Lorem ipsum is simply dummy text of the printing and typesetting industry. Lorem ipsum has been the industry's standard dummy text ever since the 1500s, when an unknown printer took a galley of type and scrambled it to make a type specimen book. It has survived not only five centuries, but</p></div>
  <div class="abs" style="left:23px;top:104px;width:60px;display:flex;gap:4px;align-items:flex-start"><b style="font-size:8px;color:var(--cyan)">2016</b><p class="body" style="position:static;text-align:left">Lorem ipsum is simply dummy text of the printing and typesetting and ate</p></div>
  <div class="abs" style="left:92px;top:104px;width:60px;display:flex;gap:4px;align-items:flex-start"><b style="font-size:8px;color:var(--orange)">2017</b><p class="body" style="position:static;text-align:left">Lorem ipsum is simply dummy text of the printing and typesetting and ate</p></div>
  <div class="abs" style="left:23px;top:134px;width:60px;display:flex;gap:4px;align-items:flex-start"><b style="font-size:8px;color:var(--orange)">2018</b><p class="body" style="position:static;text-align:left">Lorem ipsum is simply dummy text of the printing and typesetting and ate</p></div>
  <div class="abs" style="left:92px;top:134px;width:60px;display:flex;gap:4px;align-items:flex-start"><b style="font-size:8px;color:var(--green)">2019</b><p class="body" style="position:static;text-align:left">Lorem ipsum is simply dummy text of the printing and typesetting and ate</p></div>
  <svg class="abs" style="left:168px;top:54px" width="120" height="108" viewBox="-60 -52 120 108" font-family="Carlito,sans-serif">
    <path d="M0 0 L0 -36 A36 36 0 1 1 -17.3 31.5 Z" fill="var(--teal)"/>
    <g transform="translate(-5 2)"><path d="M0 0 L-17.3 31.5 A36 36 0 0 1 -33.5 -13.3 Z" fill="var(--orange)"/></g>
    <g transform="translate(-8 -5)"><path d="M0 0 L-33.5 -13.3 A36 36 0 0 1 -19.3 -30.4 Z" fill="var(--yellow)"/></g>
    <g transform="translate(-3 -8)"><path d="M0 0 L-19.3 -30.4 A36 36 0 0 1 0 -36 Z" fill="var(--green)"/></g>
    <g font-size="2.8" fill="#fff" text-anchor="middle"><text x="18" y="4">58%</text><text x="-27" y="12">23%</text><text x="-28" y="-23">10%</text><text x="-10" y="-32">9%</text></g>
    <g font-size="2.4" fill="#555"><rect x="-36" y="49" width="2" height="2" fill="var(--teal)"/><text x="-33" y="51">2016</text><rect x="-24" y="49" width="2" height="2" fill="var(--orange)"/><text x="-21" y="51">2017</text><rect x="-12" y="49" width="2" height="2" fill="var(--yellow)"/><text x="-9" y="51">2018</text><rect x="0" y="49" width="2" height="2" fill="var(--green)"/><text x="3" y="51">2019</text></g>
  </svg>
  <p class="foot">Hospitality project name here</p><div class="foot-line"></div><p class="pnum">18</p>
</section>

</body>
</html>
```